TuneRoost - Music Industry App needs a top quality wordpress homepage

We need a modern responsive wordpress homepage built. Our website will only feature one page with the goal to get people to sign up to our app. A word document has been uploaded outlining the page content/sections.

Once the homepage is finalised, I will also need 2 landing pages built as part of this competition. It will be very similar to the homepage with the same layout etc but just feature different images and content. The homepage is for anyone (artists and venues) to find out about us but the landing pages will be artist or venue specific.

The completed work must be delivered as an exportable file into wordpress and be designed properly so no more work is needed to begin utilising as the actual website. The images used must be setup correctly for speed and quality also.

Target Market(s)

Venues and Artists.

Coding

Coded - Design and coding required

Requirements
Must have
• UPDATE: High Res Logo files attached
• Must be a modern looking website and be responsive. Must look good across all devices from desktop, to mobile and tablet. Needs to be very high quality.
• Please see the attached logo - I am waiting for the final high quality version and will reupload when complete but this will be enough to get you started for now. The website must have a dark base colour and have red/white elements to match the logo. The red colour used MUST match the red colour used in the logo.
• Please have a go at creating it how you think is best and provide feedback from there. I am leaving it very open to the designers so I can get the best website possible and lots of different ideas etc.

```html
<!DOCTYPE html>
<html lang="en">
<head>
<meta charset="utf-8">
<title>TuneRoost – Zoomly for Live Music</title>
<link rel="stylesheet" href="https://fonts.googleapis.com/css2?family=Lexend:wght@400;500&family=Open+Sans:wght@400;600;700&display=swap">
<style>
:root{
  --red:#e0021b;
  --black:#000;
  --ink:#1b1b1b;
  --white:#fff;
  --paper:#f4f1f1;
  --icon-disc:#3a3a3a;
  --head:'Lexend',sans-serif;
  --body:'Open Sans',sans-serif;
}
*{margin:0;padding:0;box-sizing:border-box}
html,body{width:1200px;height:3288px;overflow:hidden}
body{position:relative;background:var(--paper);font-family:var(--body);color:var(--ink)}
h1,h2{font-weight:400}
.abs{position:absolute}
.center{left:0;width:1200px;text-align:center}

/* hero */
.hero{top:0;left:0;width:1200px;height:725px;
  background:radial-gradient(ellipse at 35% 25%,#b06bd6 0%,#6a3aa0 25%,transparent 55%),
             radial-gradient(ellipse at 78% 20%,#e08a3a 0%,#a0442a 25%,transparent 50%),
             linear-gradient(180deg,#4a2a6e 0%,#3a1d4e 45%,#150b18 80%,#0a0508 100%)}
.brand{top:90px;display:flex;justify-content:center;align-items:center;gap:14px}
.brand-dot{width:30px;height:30px;border-radius:50%;background:var(--red)}
.brand-name{font-family:var(--head);font-weight:400;font-size:50px;color:var(--white);letter-spacing:.5px}
.hero-title{top:258px;font-family:var(--head);font-weight:500;font-size:49px;color:var(--white)}
.hero-sub{top:328px;font-family:var(--head);font-size:31px;line-height:36px;color:var(--white)}
.hero-cta{top:432px;font-family:var(--head);font-size:24px;color:var(--white)}
.signup{display:flex;align-items:center;background:var(--white)}
.signup .field{flex:1;font-size:15px;color:#444;padding-left:22px}
.signup .btn{background:var(--red);color:var(--white);display:flex;align-items:center;justify-content:center}
.hero-form{top:481px;left:354px;width:499px;height:51px;padding-right:8px}
.hero-form .btn{width:140px;height:40px;font-family:var(--head);font-size:19px}
.arrow{width:52px;height:52px;border-radius:50%;background:rgba(255,255,255,.35);display:flex;align-items:center;justify-content:center}

/* how it works */
.how{top:725px;left:0}
.how-title{top:804px;font-family:var(--head);font-weight:400;font-size:31px;color:var(--white)}
.step{width:190px;text-align:center;color:var(--white)}
.step-disc{width:94px;height:94px;border-radius:50%;background:var(--icon-disc);margin:0 auto;display:flex;align-items:center;justify-content:center}
.step-num{font-family:var(--head);font-size:35px;margin-top:20px;line-height:40px}
.step-text{font-size:15px;line-height:23px;margin-top:8px}

/* why */
.why-title{top:1307px;font-family:var(--head);font-weight:400;font-size:33px;color:#111}
.perk{width:240px;text-align:center;top:1404px}
.perk-disc{width:80px;height:80px;border-radius:50%;background:#e6e3e3;margin:0 auto;display:flex;align-items:center;justify-content:center}
.perk-dash{width:24px;height:2px;background:var(--red);margin:34px auto 0}
.perk-name{font-size:18px;font-weight:600;margin-top:16px;color:#111}
.perk-text{font-size:14px;line-height:20px;margin-top:18px;color:#222}

/* audiences */
.venues{top:1726px;left:0;width:598px;height:544px;background:linear-gradient(180deg,#2b2b2b 0%,#1c1c1c 55%,#0d0d0d 100%);color:var(--white)}
.artists{top:1726px;left:598px;width:602px;height:544px;background:linear-gradient(180deg,#c9ccd0 0%,#d4d7db 55%,#bfc3c8 100%);color:#111}
.aud-title{font-family:var(--head);font-weight:400;font-size:27px}
.aud-list{list-style:none}
.aud-list li{position:relative;padding-left:22px;font-size:16px;line-height:18px}
.aud-list li svg{position:absolute;left:2px;top:3px}
.aud-note{font-size:13.5px;line-height:19px}
.aud-form{height:40px;padding-right:5px}
.aud-form .field{font-size:11px;padding-left:18px}
.aud-form .btn{width:110px;height:30px;font-family:var(--head);font-size:14px}

/* about */
.about{top:2270px;left:0;width:1200px;height:413px;
  background:radial-gradient(ellipse at 50% 20%,#7a4a9a 0%,#4a2a5e 30%,transparent 65%),linear-gradient(180deg,#3b2446 0%,#241a28 60%,#121012 100%)}
.about-title{top:2365px;font-family:var(--head);font-weight:400;font-size:41px;color:var(--white)}
.about-text{top:2430px;left:200px;width:800px;text-align:center;font-size:14px;line-height:23px;letter-spacing:-.15px;color:#eee}

/* contact */
.contact{top:2683px;left:0;width:598px;height:516px;background:var(--red)}
.contact-title{top:2745px;left:142px;font-family:var(--head);font-weight:400;font-size:34px;color:var(--white)}
.field-line{left:143px;width:388px;border-bottom:1px solid rgba(255,255,255,.85);color:var(--white);font-size:16px;padding-bottom:4px}
.submit{top:3063px;left:147px;width:152px;height:44px;background:#0c0c0c;color:var(--white);font-family:var(--head);font-size:18px;display:flex;align-items:center;justify-content:center}
.map{top:2683px;left:598px;width:602px;height:516px;background:linear-gradient(135deg,#efefef 0%,#e6e6e6 50%,#dcdcdc 100%)}
.map-card{top:2936px;left:768px;width:283px;height:141px;background:var(--white);box-shadow:0 1px 4px rgba(0,0,0,.25);display:flex;align-items:center;justify-content:center;text-align:center;font-family:var(--head);font-size:18.5px;line-height:23px;color:#111}

/* footer */
.footer{top:3199px;left:0;width:1200px;height:89px;background:var(--black);color:var(--white);display:flex;align-items:center;justify-content:center;font-family:var(--head);font-size:15.5px}
</style>
</head>
<body>

<section class="hero abs" role="img" aria-label="Concert crowd with raised hands under purple and orange stage lights"></section>
<div class="brand abs center"><span class="brand-dot"></span><span class="brand-name">TuneRoost</span></div>
<h1 class="hero-title abs center">Zoomly for Live Music</h1>
<p class="hero-sub abs center">TuneRoost connects venues with artists to<br>make booking gigs simple</p>
<p class="hero-cta abs center">Join Now for FREE</p>
<div class="signup hero-form abs"><span class="field">Email address</span><span class="btn">Join Now</span></div>
<div class="arrow abs" style="top:343px;left:126px"><svg width="18" height="22" viewBox="0 0 18 22"><path d="M12 3 4 11l8 8" fill="none" stroke="#111" stroke-width="2.4"/></svg></div>
<div class="arrow abs" style="top:343px;left:1013px"><svg width="18" height="22" viewBox="0 0 18 22"><path d="M6 3l8 8-8 8" fill="none" stroke="#111" stroke-width="2.4"/></svg></div>

<svg class="how abs" width="1200" height="511" viewBox="0 0 1200 511"><path d="M0 0H1200V328L928 511H264L0 328Z" fill="#000"/></svg>
<h2 class="how-title abs center">How TuneRoost Works</h2>

<div class="step abs" style="top:886px;left:144px">
  <div class="step-disc"><svg width="44" height="48" viewBox="0 0 44 48" fill="none" stroke="#e0021b" stroke-width="2.6"><rect x="6" y="6" width="30" height="38" rx="3"/><path d="M12 18h18M12 25h18M12 32h12M28 4l8 8"/></svg></div>
  <div class="step-num">1</div>
  <div class="step-text">Artists and venues<br>sign up for free and<br>create a profile</div>
</div>
<div class="step abs" style="top:886px;left:325px">
  <div class="step-disc"><svg width="48" height="44" viewBox="0 0 48 44" fill="#e0021b"><path d="M14 6 30 2v24a6 6 0 1 1-3-5V10l-10 3v17a6 6 0 1 1-3-5Z"/><circle cx="38" cy="14" r="5"/><path d="M30 34c0-6 4-10 8-10s8 4 8 10Z"/></svg></div>
  <div class="step-num">2</div>
  <div class="step-text">Venues search for<br>an artist for their<br>upcoming gigs</div>
</div>
<div class="step abs" style="top:886px;left:502px">
  <div class="step-disc"><svg width="46" height="46" viewBox="0 0 46 46" fill="none" stroke="#e0021b" stroke-width="2.6"><circle cx="23" cy="23" r="20"/><path d="M16 13l4 4-3 3c1 4 5 8 9 9l3-3 4 4-3 3c-9 0-17-8-17-17Z"/></svg></div>
  <div class="step-num">3</div>
  <div class="step-text">Venues request a<br>quote and communicate<br>with the artist direct</div>
</div>
<div class="step abs" style="top:886px;left:689px">
  <div class="step-disc"><svg width="54" height="44" viewBox="0 0 54 44" fill="none" stroke="#e0021b" stroke-width="2.4"><rect x="6" y="6" width="26" height="16" rx="2"/><path d="M4 28h14l10 6 12-4"/><circle cx="40" cy="26" r="9"/><path d="M40 20v12M37 23h5a2 2 0 0 1 0 4h-4a2 2 0 0 0 0 4h5"/></svg></div>
  <div class="step-num">4</div>
  <div class="step-text">The gig is booked in<br>once payment is<br>provided by the venue.</div>
</div>
<div class="step abs" style="top:886px;left:870px">
  <div class="step-disc"><svg width="50" height="44" viewBox="0 0 50 44" fill="none" stroke="#e0021b" stroke-width="2.6"><circle cx="30" cy="22" r="16"/><path d="M30 12v10l7 5M4 16h10M2 24h10M6 32h8"/></svg></div>
  <div class="step-num">5</div>
  <div class="step-text">Upon completion the<br>money is paid to the artist<br>within 48 hours or less.</div>
</div>

<h2 class="why-title abs center">Why TuneRoost?</h2>
<div class="perk abs" style="left:124px">
  <div class="perk-disc"><svg width="50" height="46" viewBox="0 0 50 46" fill="none" stroke="#e0021b" stroke-width="2.4"><rect x="4" y="4" width="36" height="32" rx="2"/><path d="M4 11h36M10 18h10M10 24h8M10 30h10"/><circle cx="32" cy="24" r="7"/><path d="M29 24l2 2 4-4M36 30l8 10"/></svg></div>
  <div class="perk-dash"></div><div class="perk-name">Simple</div>
  <div class="perk-text">TuneRoost makes gig<br>booking easy for both the<br>venue and artist.</div>
</div>
<div class="perk abs" style="left:369px">
  <div class="perk-disc"><svg width="60" height="40" viewBox="0 0 60 40" fill="#e0021b"><path d="M0 4h10l4 18H4Z"/><path d="M60 4H50l-4 18h10Z"/><path d="M14 8l10-4 8 3 8-3 8 4-2 14-12 12c-2 2-5 1-5-1l-3 2c-2 1-4 0-4-2-2 1-4 0-4-2l-4-4Z"/></svg></div>
  <div class="perk-dash"></div><div class="perk-name">Connect</div>
  <div class="perk-text">Join the TuneRoost community<br>which is full of amazing<br>artists and venues.</div>
</div>
<div class="perk abs" style="left:620px">
  <div class="perk-disc"><svg width="44" height="50" viewBox="0 0 44 50"><path d="M22 2 40 8v16c0 12-8 20-18 24C12 44 4 36 4 24V8Z" fill="#e0021b"/><path d="M13 24l7 7 12-14" fill="none" stroke="#fff" stroke-width="4"/></svg></div>
  <div class="perk-dash"></div><div class="perk-name">Protection</div>
  <div class="perk-text">Everyone is protected<br>with our complimentary<br>dispute resolutions.</div>
</div>
<div class="perk abs" style="left:862px">
  <div class="perk-disc"><svg width="50" height="50" viewBox="0 0 50 50"><circle cx="28" cy="14" r="11" fill="#e0021b"/><text x="28" y="19" text-anchor="middle" font-family="Open Sans,sans-serif" font-size="14" font-weight="700" fill="#fff">$</text><path d="M4 34h12l8 4h10l12-8 2 3-14 11H18l-8-3H4Z" fill="#e0021b"/></svg></div>
  <div class="perk-dash"></div><div class="perk-name">Price</div>
  <div class="perk-text">Get the best rate possible<br>with TuneRoost only receiving<br>5% of the artists fee.</div>
</div>

<section class="venues abs" role="img" aria-label="Dark crowd silhouettes in front of a stage"></section>
<h2 class="aud-title abs" style="top:1784px;left:162px;color:#fff">Venues</h2>
<ul class="aud-list abs" style="top:1840px;left:162px;width:400px;color:#fff">
  <li style="margin-bottom:8px"><svg width="10" height="12"><path d="M2 1l5 5-5 5" fill="none" stroke="#fff" stroke-width="2"/></svg>TuneRoost is a 100% FREE service for all venues - you pay us nothing!</li>
  <li style="margin-bottom:8px"><svg width="10" height="12"><path d="M2 1l5 5-5 5" fill="none" stroke="#fff" stroke-width="2"/></svg>Get instant access to hundreds of artists around your local community</li>
  <li style="margin-bottom:8px"><svg width="10" height="12"><path d="M2 1l5 5-5 5" fill="none" stroke="#fff" stroke-width="2"/></svg>All genres to suit any venue from a pub to a wedding or even a nightclub</li>
  <li style="margin-bottom:8px"><svg width="10" height="12"><path d="M2 1l5 5-5 5" fill="none" stroke="#fff" stroke-width="2"/></svg>Simple booking process with a money back guarantee</li>
  <li><svg width="10" height="12"><path d="M2 1l5 5-5 5" fill="none" stroke="#fff" stroke-width="2"/></svg>Communicate directly with the artist and negotiate the price</li>
</ul>
<p class="aud-note abs" style="top:2070px;left:162px;width:380px;color:#fff">TuneRoost is not yet ready to host gigs as we're currently working on building our artists. We are launching for venues in Q4 2019. Pre-register now to keep informed and be one of the first people to use our platform.</p>
<div class="signup aud-form abs" style="top:2167px;left:162px;width:385px"><span class="field">Email address</span><span class="btn">Pre-Register</span></div>

<section class="artists abs" role="img" aria-label="Performer on a stage above a large festival crowd in pale light"></section>
<h2 class="aud-title abs" style="top:1794px;left:660px">Artists</h2>
<ul class="aud-list abs" style="top:1849px;left:660px;width:400px">
  <li style="margin-bottom:16px"><svg width="10" height="12"><path d="M2 1l5 5-5 5" fill="none" stroke="#e0021b" stroke-width="2"/></svg>Sign up to TuneRoost for FREE and get yourself in front of venues</li>
  <li style="margin-bottom:16px"><svg width="10" height="12"><path d="M2 1l5 5-5 5" fill="none" stroke="#e0021b" stroke-width="2"/></svg>Only pay us if you get a gig - we only get 5% of the fee you charge the venue</li>
  <li style="margin-bottom:16px"><svg width="10" height="12"><path d="M2 1l5 5-5 5" fill="none" stroke="#e0021b" stroke-width="2"/></svg>All genres and artists welcome - as long as you're experienced and professional</li>
  <li style="margin-bottom:16px"><svg width="10" height="12"><path d="M2 1l5 5-5 5" fill="none" stroke="#e0021b" stroke-width="2"/></svg>Get paid within 48 hours or less after the gig guaranteed!</li>
  <li><svg width="10" height="12"><path d="M2 1l5 5-5 5" fill="none" stroke="#e0021b" stroke-width="2"/></svg>Negotiate your price and don't pay huge agent fees to ensure you earn top dollar</li>
</ul>
<p class="abs" style="top:2125px;left:659px;font-size:17px;color:#111">Sign up and create your TuneRoost profile now</p>
<div class="signup aud-form abs" style="top:2164px;left:660px;width:385px"><span class="field">Email address</span><span class="btn">Join Now</span></div>

<section class="about abs" role="img" aria-label="Crowd at a concert lit by violet stage beams"></section>
<h2 class="about-title abs center">About TuneRoost</h2>
<p class="about-text abs">Lorem ipsum is a pseudo-Latin text used in web design, typography, layout, and printing in place of English to emphasise design elements over content. It's also called placeholder (or filler) text. It's a convenient tool for mock-ups. It helps to outline the visual elements of a document or presentation, eg typography, font, or layout. Lorem ipsum is mostly a part of a Latin text by the ancient author and thinker Varrenus. Its words and letters have been changed by addition or removal, so to deliberately render its content nonsensical; it's not genuine, correct</p>

<section class="contact abs"></section>
<h2 class="contact-title abs">Contact Us</h2>
<div class="field-line abs" style="top:2806px">Name *</div>
<div class="field-line abs" style="top:2850px">Company</div>
<div class="field-line abs" style="top:2900px">E-mail *</div>
<div class="field-line abs" style="top:2945px">Phone Number</div>
<div class="field-line abs" style="top:2988px;height:55px">Message</div>
<div class="submit abs">Submit</div>

<section class="map abs" role="img" aria-label="Street map of the Fernvale area"></section>
<svg class="abs" style="top:2858px;left:893px" width="36" height="48" viewBox="0 0 36 48"><path d="M18 2C9 2 2 9 2 18c0 12 16 28 16 28s16-16 16-28C34 9 27 2 18 2Z" fill="#e0021b"/><circle cx="18" cy="18" r="6" fill="#fff"/></svg>
<div class="map-card abs">Fernvale, New<br>South Wales, Australia</div>

<footer class="footer abs">© 2019 TuneRoost&nbsp; All right reserved&nbsp; |&nbsp; Privacy Policy</footer>

</body>
</html>
```